ULMIRA card Technical Architecture

Hello everyone ULMIRA: It is a consulting firm in Architecture and Construction. I require a card duplexing, sober, elegant, classic but not boring. Update 1: Use the following data for the card. Name: Gonzalo Pereda Mauricio Villalta Position: COO Twitter: @ulmiraAT Homepage: ulmira-example.com home address not include the participation of all thank you.

Target Market(s)

Construction companies, Architects and Consulting Engineers

Industry/Entity Type

Consulting

Contact Information for Business Card

Los campos que debe tener:
Nombre, Cargo, email, homepage y twitter

Font styles to use
Serif
Sans Serif
Other font styles liked:
• Me gustan playfair display, open sans y roboto, pero estoy sujeto a sus propuestas

Requirements
Must have
• Colors: Present combined proposals in white, red, gray and black Update 1: The two names must be clearly differentiated from the two surnames
Nice to have
• They are free to present their best proposals. I will bring them immediate feedback to the extent you can go see their designs. Complete data for card and logo files will give the winner the

```html
<!DOCTYPE html>
<html lang="es">
<head>
<meta charset="utf-8">
<title>ULMIRA – Tarjeta de presentación</title>
<link rel="stylesheet" href="https://fonts.googleapis.com/css2?family=Montserrat:wght@400;500;700&family=Open+Sans:wght@400;600&display=swap">
<style>
  :root {
    --stage: #d9d9db;
    --black: #050505;
    --white: #ffffff;
    --red: #c8161e;
    --red-deep: #7a0d14;
    --maroon: #6e1017;
    --gray-text: #2b2b2b;
    --gray-line: #3a3a3a;
    --gray-soft: #8a8a8a;
  }
  * { box-sizing: border-box; margin: 0; padding: 0; }
  html, body {
    width: 1200px; height: 900px; overflow: hidden;
    background: var(--stage);
  }
  .canvas {
    position: relative; width: 1200px; height: 900px;
    display: flex; flex-direction: column; align-items: center; justify-content: center;
    gap: 36px;
  }
  .card {
    position: relative; width: 680px; height: 388px;
    border-radius: 22px; overflow: hidden;
    box-shadow: 0 10px 28px rgba(0,0,0,.25);
  }

  /* Back side */
  .card--back { background: var(--black); color: var(--white); }
  .brand-block {
    position: absolute; left: 50%; top: 50%;
    transform: translate(-50%, -50%);
    text-align: center;
  }
  .brand-name {
    font-family: "Montserrat", sans-serif; font-weight: 500;
    font-size: 70px; letter-spacing: 22px; margin-right: -22px;
    color: var(--white); line-height: 1;
  }
  .brand-rule {
    height: 1px; background: var(--gray-soft); margin: 14px 0 10px;
  }
  .brand-tagline {
    font-family: "Montserrat", sans-serif; font-weight: 400;
    font-size: 20px; letter-spacing: 7px; margin-right: -7px;
    color: var(--red);
  }
  .social {
    position: absolute; right: 30px; top: 32px;
    display: flex; align-items: center; gap: 9px;
    font-family: "Open Sans", sans-serif; font-size: 15px; color: var(--white);
  }
  .social-dot { width: 12px; height: 12px; border-radius: 50%; background: var(--white); }

  /* Front side */
  .card--front { background: var(--white); }
  .front-mark {
    position: absolute; left: 0; top: 0; width: 300px; height: 330px;
    display: flex; align-items: center; justify-content: center;
  }
  .front-mark-name {
    font-family: "Montserrat", sans-serif; font-weight: 700;
    font-size: 40px; letter-spacing: 6px; color: var(--red);
  }
  .divider {
    position: absolute; left: 312px; top: 70px; width: 1px; height: 190px;
    background: linear-gradient(to bottom, transparent, var(--gray-line) 20%, var(--gray-line) 80%, transparent);
  }
  .contact {
    position: absolute; left: 340px; top: 72px;
    font-family: "Open Sans", sans-serif; color: var(--gray-text);
  }
  .person-given, .person-family {
    font-family: "Montserrat", sans-serif; font-weight: 700;
    font-size: 25px; color: var(--maroon); line-height: 1.15;
  }
  .person-role { font-size: 15px; line-height: 1.3; margin-bottom: 4px; }
  .person-family { margin-top: 2px; }
  .person-title { font-size: 15px; margin-bottom: 12px; }
  .contact-list { list-style: none; }
  .contact-item {
    display: flex; align-items: center; gap: 10px;
    font-size: 16px; line-height: 1.5;
  }
  .contact-item svg { width: 13px; height: 13px; flex: none; }
  .front-band { position: absolute; left: 0; bottom: 0; width: 680px; height: 90px; }
</style>
</head>
<body>
<main class="canvas">

  <section class="card card--back" aria-label="Reverso de la tarjeta">
    <div class="brand-block">
      <div class="brand-name">ULMIRA</div>
      <div class="brand-rule"></div>
      <div class="brand-tagline">ARQUITECTURA TÉCNICA</div>
    </div>
    <div class="social">
      <span class="social-dot"></span>
      <span class="social-handle">@ulmiraAT</span>
    </div>
  </section>

  <section class="card card--front" aria-label="Anverso de la tarjeta">
    <div class="front-mark"><span class="front-mark-name">ULMIRA</span></div>
    <div class="divider"></div>

    <div class="contact">
      <div class="person-given">Mauricio Gonzalo</div>
      <div class="person-role">COO</div>
      <div class="person-family">Pereda Villalta</div>
      <div class="person-title">Director de Operaciones</div>
      <ul class="contact-list">
        <li class="contact-item">
          <svg viewBox="0 0 16 16" aria-hidden="true"><path d="M3 1.5l3 .5 1 3-2 1.5a9 9 0 0 0 4.5 4.5L11 9l3 1 .5 3-2 1.5C7 14 2 9 1.5 3.5z" fill="var(--red)"/></svg>
          <span>(+571) 555 010 2040</span>
        </li>
        <li class="contact-item">
          <svg viewBox="0 0 16 16" aria-hidden="true"><rect x="1.5" y="3.5" width="13" height="9" fill="none" stroke="var(--red)" stroke-width="1.6"/><path d="M1.5 3.5L8 9l6.5-5.5" fill="none" stroke="var(--red)" stroke-width="1.6"/></svg>
          <span>info@ulmira-example.com</span>
        </li>
        <li class="contact-item">
          <svg viewBox="0 0 16 16" aria-hidden="true"><circle cx="8" cy="8" r="6.5" fill="none" stroke="var(--red)" stroke-width="1.4"/><ellipse cx="8" cy="8" rx="2.8" ry="6.5" fill="none" stroke="var(--red)" stroke-width="1.2"/><path d="M1.5 8h13" stroke="var(--red)" stroke-width="1.2"/></svg>
          <span>www.ulmira-example.com</span>
        </li>
      </ul>
    </div>

    <svg class="front-band" viewBox="0 0 680 90" preserveAspectRatio="none" aria-hidden="true">
      <defs>
        <linearGradient id="bandRed" x1="0" y1="0" x2="1" y2="0">
          <stop offset="0" stop-color="var(--red-deep)"/>
          <stop offset="1" stop-color="var(--red)"/>
        </linearGradient>
      </defs>
      <polygon points="470,40 680,40 680,90 0,90 0,82 440,82" fill="url(#bandRed)"/>
      <polygon points="455,36 470,36 446,80 432,80" fill="var(--red)"/>
    </svg>
  </section>

</main>
</body>
</html>
```